Coastline Premier Retreats Business Card Design

Design a business card for Coastline Premier Retreats. Look at the website for colors and reference. Card should have logo, name, title, office number, mobile number, email, URL and a tagline like, "Luxury Hotel & Resort Email Marketing" (This might change).

https://www.coastlinepremierretreats.example

The rest I will leave up to your imagination.

Contact Information for Business Card

Logo, name, title, office number, mobile number, email, URL and a tagline like, "Luxury Hotel & Resort Email Marketing" (This might change).

```html
<!DOCTYPE html>
<html lang="en">
<head>
<meta charset="utf-8">
<title>Coastline Premier Retreats — Business Card</title>
<link href="https://fonts.googleapis.com/css2?family=Montserrat:wght@400;500;700;800&display=swap" rel="stylesheet">
<style>
  :root {
    --card: #1c1c1c;
    --orange: #f57c12;
    --white: #ffffff;
    --muted: #e6e6e6;
  }
  * { margin: 0; padding: 0; box-sizing: border-box; }
  html, body {
    width: 1200px; height: 802px; overflow: hidden;
    background: linear-gradient(180deg, #d2d2d2 0%, #a9a9a9 100%);
    font-family: "Montserrat", sans-serif;
  }
  .stage {
    width: 1200px; height: 802px;
    display: flex; flex-direction: column; align-items: center; justify-content: center;
    gap: 40px;
  }
  .card {
    position: relative;
    width: 560px; height: 320px;
    background: var(--card);
    border-radius: 22px;
    color: var(--white);
    box-shadow: 0 14px 30px rgba(0,0,0,.35);
    overflow: hidden;
  }

  /* contact side */
  .brand-mark {
    display: flex; align-items: center; gap: 10px;
    font-weight: 700; color: var(--white);
    text-transform: uppercase; letter-spacing: .04em;
  }
  .brand-mark .dot {
    width: 10px; height: 10px; background: var(--orange); flex: none;
  }
  .card--contact .brand-mark {
    position: absolute; left: 40px; top: 48px;
    font-size: 15px; line-height: 1.2; width: 190px;
  }
  .person { position: absolute; left: 40px; bottom: 50px; }
  .person__name {
    font-weight: 800; font-size: 26px; color: var(--orange);
    letter-spacing: .02em; text-transform: uppercase;
  }
  .person__title { font-size: 14px; color: var(--muted); margin-top: 4px; }

  .contact {
    position: absolute; left: 256px; right: 26px; top: 48px;
    font-size: 11.5px; line-height: 1.6; color: var(--white);
  }
  .contact__address { margin-bottom: 16px; }
  .contact__list { list-style: none; }
  .contact__list li { display: flex; align-items: center; gap: 8px; white-space: nowrap; }
  .contact__list svg { width: 11px; height: 11px; flex: none; fill: var(--orange); }
  .contact__list .accent { color: var(--orange); }

  /* front side */
  .card--front {
    display: flex; flex-direction: column; align-items: center; justify-content: center;
    padding: 0 24px;
  }
  .card--front .brand-mark { font-size: 26px; gap: 14px; white-space: nowrap; }
  .card--front .brand-mark .dot { width: 15px; height: 15px; }
  .tagline {
    margin-top: 40px; font-weight: 500; font-size: 17px;
    color: var(--orange); letter-spacing: .02em;
  }
</style>
</head>
<body>
<main class="stage">

  <section class="card card--contact" aria-label="Business card, contact side">
    <div class="brand-mark"><span class="dot"></span><span>Coastline Premier Retreats</span></div>

    <div class="person">
      <p class="person__name">Daniel Moreau</p>
      <p class="person__title">CEO/Founder</p>
    </div>

    <div class="contact">
      <p class="contact__address">Po Box, 48 Harbor Lane<br>Seabright, CL 20415</p>
      <ul class="contact__list">
        <li>
          <svg viewBox="0 0 12 12" aria-hidden="true"><path d="M3 0h6a1 1 0 0 1 1 1v10a1 1 0 0 1-1 1H3a1 1 0 0 1-1-1V1a1 1 0 0 1 1-1zm0 1.5v8h6v-8z"/></svg>
          555.204.7100
        </li>
        <li>
          <svg viewBox="0 0 12 12" aria-hidden="true"><path d="M2.5 0.5l2 2.5-1.2 1.3a7 7 0 0 0 4.4 4.4L9 7.5l2.5 2-1 1.8C5.5 11.5 0.5 6.5 0.7 1.5z"/></svg>
          +34 600 555 214
        </li>
        <li>
          <svg viewBox="0 0 12 12" aria-hidden="true"><path d="M0 2h12v8H0zm1.2 1L6 6.5 10.8 3z"/></svg>
          info@coastlinepremierretreats.example
        </li>
        <li>
          <svg viewBox="0 0 12 12" aria-hidden="true"><circle cx="6" cy="6" r="5.5"/></svg>
          <span>www.<span class="accent">coastlinepremierretreats</span>.example</span>
        </li>
      </ul>
    </div>
  </section>

  <section class="card card--front" aria-label="Business card, front side">
    <div class="brand-mark"><span class="dot"></span><span>Coastline Premier Retreats</span></div>
    <p class="tagline">Luxury Hotel &amp; Resort Email Marketing</p>
  </section>

</main>
</body>
</html>
```